NZ First of it's kind solutions directory and marketplace for busy Mums needs a business card design

We need a business card design for our new nationwide business in NZ (long term plans to go global). We provide solutions to the everyday challenges that busy Mums face by connecting them with quality communities and suppliers of carefully selected, relevant products and services. We sell direct via our online marketplace. The final design should communicate our values of inclusivity, quality and smart solutions. Colours should incorporate our logo colour palette of #477077 and #6ba8b2. Our website is at https://www.brightnestmums.example

Target Market(s)

busy Mums, Age 28 – 50, female, income over $100K, location main centres NZ primarily but NZ wide. Is likely juggling work or career with a young family. Probably had hobbies which have fallen by the wayside.
-Wants to succeed in her chosen career without compromising on family life
-to successfully juggle her career without feeling like she is compromising her children
- Is time poor, something always has to give and it’s generally her health (she’ll stay up late, get stressed)
- probably ex corporate or professional career. Has discretional income

Industry/Entity Type

Business

Contact Information for Business Card

Lena Forbisher, Founder, BrightNestMums.example (Strapline Tap; Gather; Sorted), 47 Kowhai Terrace, Ellerslie, Auckland 1051, New Zealand. Mob: 021 483 517 Ph: +64 (0)9 571 4860

Font styles to use
Other font styles liked:
• Raleway, and/or Architects Daughter

Colors
00a990
33b8a4
86cfc6
cfeae6

Requirements
Must have
• the above details, streamline. the logo and colours associated with those logos
Should not have
• foil or metallic colours

```html
<!DOCTYPE html>
<html lang="en">
<head>
<meta charset="utf-8">
<title>BrightNestMums – Business Card</title>
<link href="https://fonts.googleapis.com/css2?family=Roboto+Condensed:wght@400;700&family=Roboto:wght@400&display=swap" rel="stylesheet">
<style>
  :root {
    --backdrop: #2a2a2a;
    --paper: #f1f1f1;
    --teal-deep: #477077;
    --teal-light: #6ba8b2;
    --ink-grey: #4a4a4a;
    --white: #ffffff;
  }
  * { margin: 0; padding: 0; box-sizing: border-box; }
  html, body { width: 1200px; height: 960px; overflow: hidden; }
  body { background: var(--backdrop); position: relative; font-family: "Roboto", Arial, sans-serif; }

  .card {
    position: absolute;
    width: 600px; height: 342px;
    border-radius: 20px;
    background: var(--paper);
    overflow: hidden;
    box-shadow: 0 4px 10px rgba(0,0,0,.45);
  }
  .card--front { left: 314px; top: 113px; }
  .card--back  { left: 311px; top: 472px; }

  .card__wave { position: absolute; inset: 0; }

  .brand {
    position: absolute;
    display: flex; align-items: center; gap: 12px;
    font-family: "Roboto Condensed", Arial, sans-serif;
    font-weight: 700;
    color: var(--teal-deep);
    letter-spacing: -0.5px;
  }
  .brand__dot { border-radius: 50%; background: var(--teal-light); flex: none; }
  .card--front .brand { left: 54px; top: 58px; font-size: 38px; }
  .card--front .brand__dot { width: 34px; height: 34px; }

  .person { position: absolute; left: 106px; top: 134px; font-family: "Roboto Condensed", Arial, sans-serif; }
  .person__name { font-size: 22px; font-weight: 700; color: var(--teal-deep); text-transform: uppercase; line-height: 1; }
  .person__role { font-size: 16px; color: var(--teal-light); text-transform: uppercase; margin-top: 5px; }

  .contact {
    position: absolute; right: 26px; top: 223px;
    color: var(--white); font-size: 14px; text-align: right; line-height: 19px;
  }
  .contact__row { display: flex; justify-content: flex-end; align-items: center; gap: 6px; }
  .contact__icon { width: 14px; height: 14px; flex: none; }
  .contact__address { margin-top: 6px; padding-right: 0; }

  .card--back .brand { left: 51px; top: 236px; font-size: 46px; }
  .tagline {
    position: absolute; left: 192px; top: 288px;
    font-family: "Roboto Condensed", Arial, sans-serif;
    font-size: 14px; color: var(--ink-grey); text-transform: uppercase; letter-spacing: .3px;
  }
</style>
</head>
<body>

<section class="card card--front">
  <svg class="card__wave" viewBox="0 0 600 342" width="600" height="342" aria-hidden="true">
    <rect width="600" height="342" fill="var(--teal-deep)"/>
    <path d="M0,0 H600 V67 C480,170 390,305 231,304 C120,303 40,220 0,137 Z" fill="var(--teal-light)"/>
    <path d="M0,0 H600 V67 C480,160 380,292 231,292 C120,292 40,210 0,137 Z" fill="var(--paper)" stroke="var(--white)" stroke-width="3"/>
  </svg>

  <div class="brand"><span class="brand__dot"></span>BrightNestMums</div>

  <div class="person">
    <p class="person__name">Lena Forbisher</p>
    <p class="person__role">Founder</p>
  </div>

  <div class="contact">
    <p class="contact__row">+64 (0)9 571 4860
      <svg class="contact__icon" viewBox="0 0 16 16"><path fill="#fff" d="M3.5 1l2.5 3-1.5 2c1 2 3 4 5 5l2-1.5 3 2.5-1.5 2.5C8 15 1 8 1 2.5z"/></svg></p>
    <p class="contact__row">021 483 517
      <svg class="contact__icon" viewBox="0 0 16 16"><rect x="4" y="1" width="8" height="14" rx="1.5" fill="none" stroke="#fff" stroke-width="1.6"/><circle cx="8" cy="12.5" r=".9" fill="#fff"/></svg></p>
    <p class="contact__row">BrightNestMums.example
      <svg class="contact__icon" viewBox="0 0 16 16"><circle cx="8" cy="8" r="6.5" fill="none" stroke="#fff" stroke-width="1.5"/><path d="M1.5 8h13M8 1.5c-3 3-3 10 0 13M8 1.5c3 3 3 10 0 13" fill="none" stroke="#fff" stroke-width="1.2"/></svg></p>
    <p class="contact__address">47 Kowhai Terrace, Ellerslie<br>Auckland 1051, New Zealand.</p>
  </div>
</section>

<section class="card card--back">
  <div class="brand"><span class="brand__dot" style="width:40px;height:40px"></span>BrightNestMums</div>
  <p class="tagline">Tap; Gather; Sorted</p>
</section>

</body>
</html>
```